Halvorsen Construction Needs a Business Card

Our current business card is very bland, and since we have a new logo, we would like a new business card design to reflect our company. It can be a single-sided or two-sided card, but it is important that our contact information appears on the same side. I am attaching a copy of our old card and our new logo. If you need the logo in another format than the one I'm sending, please let me know. This is the information that we must have on our card, but not necessarily in any specific order:
1) Our logo
2) General Contractor
3) Derek Halvorsen, Owner
4) 482 Commerce Ridge Road, Millbrook, Alabama 35871
5) Office: 256-384-7150
7) Fax: 256-384-7151
8) Cell: 256-619-7150
9) halvorsenconstruction@qrm.net
10) halvorsenconstruction.com (can be omitted if necessary)
Also, I will need files in a format that I can alter if any of the above information changes in the near future. Thank you in advance for your submissions!
Target Market(s)
Commercial and residential clients, architects, and subcontractors.
Industry/Entity Type
Business

```html
<!DOCTYPE html>
<html lang="en">
<head>
<meta charset="utf-8">
<title>Halvorsen Construction – Business Card</title>
<link rel="stylesheet" href="https://fonts.googleapis.com/css2?family=Source+Sans+3:wght@400;600;700&display=swap">
<style>
  :root {
    --stage: #3b3b3b;
    --card-dark: #0c0c0c;
    --card-mid: #1e1e1e;
    --yellow: #f6c400;
    --white: #ffffff;
    --band: #ffffff;
    --band-tint: #fbe9a0;
  }
  * { margin: 0; padding: 0; box-sizing: border-box; }
  html, body {
    width: 1200px; height: 750px; overflow: hidden;
    background: var(--stage);
    font-family: "Source Sans 3", "Myriad Pro", Arial, sans-serif;
  }
  .card {
    position: absolute; left: 100px; top: 88px;
    width: 1000px; height: 574px;
    border-radius: 40px; overflow: hidden;
    background: linear-gradient(160deg, var(--card-mid) 0%, var(--card-dark) 70%);
    box-shadow: 0 6px 18px rgba(0,0,0,.45);
  }
  .brand { position: absolute; left: 50px; top: 32px; display: flex; align-items: center; gap: 26px; }
  .brand-square { width: 140px; height: 140px; border: 12px solid var(--white); }
  .brand-name {
    color: var(--white); font-weight: 700; font-size: 54px; line-height: 1;
    text-transform: uppercase; letter-spacing: 1px;
  }
  .person { position: absolute; left: 101px; top: 208px; color: var(--white); }
  .person-name { color: var(--yellow); font-size: 34px; line-height: 40px; }
  .person-role { font-size: 27px; line-height: 32px; }
  .contact { position: absolute; left: 442px; top: 210px; color: var(--white); }
  .address { color: var(--yellow); font-size: 27px; line-height: 31px; margin-bottom: 6px; }
  .contact-row { display: flex; align-items: center; height: 30.5px; font-size: 27px; }
  .contact-icon { width: 59px; display: flex; align-items: center; color: var(--yellow); font-size: 25px; padding-left: 6px; }
  .contact-icon svg { width: 22px; height: 22px; fill: var(--yellow); }
  .equipment-band {
    position: absolute; left: 0; bottom: 0; width: 100%; height: 128px;
    background: linear-gradient(90deg, var(--band) 0%, var(--band-tint) 50%, var(--band) 100%);
  }
</style>
</head>
<body>
  <div class="card">
    <div class="brand">
      <div class="brand-square"></div>
      <div class="brand-name">Halvorsen<br>Construction</div>
    </div>

    <div class="person">
      <div class="person-name">Derek Halvorsen</div>
      <div class="person-role">Owner</div>
      <div class="person-role">General Contractor</div>
    </div>

    <div class="contact">
      <div class="address">482 Commerce Ridge Road<br>Millbrook, Alabama 35871</div>
      <div class="contact-row">
        <span class="contact-icon"><svg viewBox="0 0 24 24"><path d="M3 9c0-3 4-5 9-5s9 2 9 5v2h-5V9c-1-.6-2.4-1-4-1s-3 .4-4 1v2H3z"/><path d="M6 13h12l2 7H4z"/></svg></span>
        <span>256-384-7150</span>
      </div>
      <div class="contact-row">
        <span class="contact-icon">Fx</span>
        <span>256-384-7151</span>
      </div>
      <div class="contact-row">
        <span class="contact-icon"><svg viewBox="0 0 24 24"><path d="M7 2h10v20H7zM9 4v14h6V4z"/></svg></span>
        <span>256-619-7150</span>
      </div>
      <div class="contact-row">
        <span class="contact-icon"><svg viewBox="0 0 24 24"><path d="M2 5h20v14H2zM4 7v1l8 5 8-5V7l-8 5z"/></svg></span>
        <span>halvorsenconstruction@qrm.net</span>
      </div>
      <div class="contact-row">
        <span class="contact-icon"><svg viewBox="0 0 24 24" fill="none"><g stroke="#f6c400" stroke-width="1.8" fill="none"><circle cx="12" cy="12" r="9"/><ellipse cx="12" cy="12" rx="4" ry="9"/><path d="M3 12h18M5 7h14M5 17h14"/></g></svg></span>
        <span>halvorsenconstruction.com</span>
      </div>
    </div>

    <div class="equipment-band" role="img" aria-label="Illustration of yellow construction equipment – excavator, crane truck and tractor – with silhouetted workers in hard hats"></div>
  </div>
</body>
</html>
```